Fitness website

Website for a fitness brand (see attached specs). Design needs to be modern and vibrant with CTAs on every page. We will provide logos, images, etc but for now user placeholder text and images. For now use the name 'Corvane Athletics' as the name to use on the design. The goal of this site is to either get people to join the gym (5 physical locations across the US); buy an online program; buy merch or supplements or sign up for the newsletter. Pleas use images from this foldeR: https://filebarn.example/share/folders/8QwTz41mKpLrXv93NdYe7HsaBuJ0Cf2_R?usp=sharing

We will be coding this in ReactNative. Lots more work for the winner as well, this is a 1st project for us.

Target Market(s)

fitness enthusiats

Industry/Entity Type

fitness, health, wellness

Number of Pages Required

5+ page

Font styles to use
Other font styles liked:
• Lato

Colors
0054AA
0677BA
7BADD7
CADEEF
E8F1F8
0094D4
00A9DD
6FCCEA
C7EBF8
E9F6FB
00AB8E
00BBA5
67D7C9
C6EFE9
E9F9F6
EE7325
F08F49
F5BC92
FAE3D3
FDF4ED

Requirements
Must have
• must be reactive. most people will view it first on mobile
Nice to have
• video in hero section of top of home page

```html
<!DOCTYPE html>
<html lang="en">
<head>
<meta charset="utf-8">
<title>Corvane Athletics — Home</title>
<link href="https://fonts.googleapis.com/css2?family=Montserrat:wght@300;600;700;800;900&family=Lato:wght@400;700&display=swap" rel="stylesheet">
<style>
:root{
  --green:#17873a;
  --blue:#1e62ae;
  --link:#1f6cb5;
  --ink:#222222;
  --dark:#2d2d2d;
  --topbar:#333333;
  --mint:#eaf3ef;
  --white:#ffffff;
  --grey:#555555;
}
*{margin:0;padding:0;box-sizing:border-box}
html,body{width:1200px;height:3755px;overflow:hidden}
body{font-family:'Lato',sans-serif;color:var(--ink);background:var(--white);position:relative}
.abs{position:absolute}
.heading{font-family:'Montserrat',sans-serif;font-weight:800;font-size:33px;letter-spacing:.5px;text-align:center;width:100%;left:0}
.rule{width:61px;height:3px;background:var(--link);left:570px}
.btn{background:var(--dark);color:var(--white);font-family:'Montserrat',sans-serif;font-weight:700;font-size:16px;border-radius:23px;display:flex;align-items:center;justify-content:center;letter-spacing:.3px}
.arrow{width:33px;height:33px;border-radius:50%;background:var(--dark);display:flex;align-items:center;justify-content:center}

/* top bar */
.topbar{top:0;left:0;width:1200px;height:35px;background:var(--topbar);color:var(--white);font-size:13px;letter-spacing:1.5px}
.topbar span{position:absolute;top:10px}
.social-dot{position:absolute;top:10px;width:14px;height:14px;border-radius:3px;background:var(--white)}

/* header */
.header{top:35px;left:0;width:1200px;height:79px;background:var(--white)}
.brand{left:111px;top:20px;font-family:'Montserrat',sans-serif;font-weight:900;font-size:31px;color:var(--ink);letter-spacing:-.5px}
.nav a{position:absolute;top:29px;font-size:15px;color:var(--ink);text-decoration:none}
.nav a.active{color:var(--link)}

/* hero */
.hero{top:114px;left:0;width:1200px;height:533px;background:var(--green);overflow:hidden}
.hero-title-light{left:111px;top:112px;font-family:'Montserrat',sans-serif;font-weight:300;font-size:48px;color:var(--white)}
.hero-title-bold{left:111px;top:172px;font-family:'Montserrat',sans-serif;font-weight:800;font-size:60px;color:var(--white);letter-spacing:-.5px}
.hero-text{left:113px;top:268px;width:472px;font-size:19px;line-height:27px;color:var(--white)}

/* locations */
.location{width:240px;text-align:center}
.loc-photo{width:160px;height:160px;border-radius:50%;border:8px solid var(--white);box-shadow:0 2px 10px rgba(0,0,0,.25);margin:0 auto}
.loc-name{font-family:'Montserrat',sans-serif;font-weight:600;font-size:21px;color:var(--link);margin-top:22px;letter-spacing:.5px}
.loc-text{font-size:15px;line-height:22px;color:var(--grey);margin:12px auto 0;width:220px}

/* about */
.about-title{left:669px;top:1318px;font-family:'Montserrat',sans-serif;font-weight:800;font-size:36px;color:var(--white);letter-spacing:.5px}
.about-text{left:669px;top:1412px;width:418px;font-size:15.5px;line-height:24px;color:var(--white);text-align:justify}

/* programs */
.program{top:1922px;width:302px;height:404px;background:var(--blue);text-align:center;color:var(--white)}
.program-photo{width:302px;height:188px}
.program h3{font-family:'Montserrat',sans-serif;font-weight:800;font-size:21px;margin-top:36px;letter-spacing:.5px}
.program p{font-size:15px;line-height:19px;margin:16px auto 0;width:260px}
.program .btn{width:153px;height:38px;margin:24px auto 0;font-size:15px}

/* testimonials */
.quote-card{left:131px;top:2608px;width:949px;height:193px;background:var(--white);border-radius:10px;box-shadow:0 2px 12px rgba(0,0,0,.08);text-align:center}
.quote-card p{font-size:15px;line-height:21.5px;color:#444;width:820px;margin:30px auto 0}
.quote-name{font-family:'Montserrat',sans-serif;font-weight:700;font-size:22px;color:var(--link);margin-top:10px;letter-spacing:.5px}
.avatar{top:2843px;width:52px;height:52px;border-radius:50%;border:4px solid var(--white);box-shadow:0 1px 5px rgba(0,0,0,.25)}

/* newsletter */
.newsletter{top:2987px;left:0;width:1200px;height:412px;background:var(--green)}
.news-text{top:3164px;left:0;width:1200px;text-align:center;font-size:18.5px;line-height:29px;color:var(--white);letter-spacing:.3px}
.email-input{left:283px;top:3254px;width:446px;height:46px;border-radius:23px;background:var(--white);font-size:15px;color:#666;padding:14px 26px;letter-spacing:.3px}

/* contact */
.contact-head{font-family:'Montserrat',sans-serif;font-weight:700;font-size:20px;color:var(--ink)}
.contact-text{font-size:15px;line-height:19px;color:var(--ink)}
.footer-social{top:3604px;width:32px;height:32px;border-radius:7px;background:var(--ink)}
.footer{top:3721px;left:0;width:1200px;height:34px;background:var(--dark);color:var(--white);font-size:13px;text-align:center;line-height:34px}
</style>
</head>
<body>

<!-- top bar -->
<div class="abs topbar">
  <span style="left:640px">Call Us:  +1 555 014 2290</span>
  <span style="left:894px">Follow Us:</span>
  <div class="social-dot" style="left:996px"></div>
  <div class="social-dot" style="left:1031px"></div>
  <div class="social-dot" style="left:1073px"></div>
</div>

<!-- header -->
<header class="abs header">
  <div class="abs brand">CORVANE ATHLETICS</div>
  <nav class="nav">
    <a class="active" style="left:572px">Home</a>
    <a style="left:655px">About</a>
    <a style="left:738px">Programs</a>
    <a style="left:847px">Shop</a>
    <a style="left:921px">Locations</a>
    <a style="left:1031px">Contact</a>
  </nav>
</header>

<!-- hero -->
<section class="abs hero">
  <svg class="abs" style="left:0;top:0" width="1200" height="533" role="img" aria-label="Photo of an athlete doing dips on a gym rig">
    <defs>
      <linearGradient id="heroPhoto" x1="0" y1="0" x2="1" y2="1">
        <stop offset="0" stop-color="#2b2d31"/>
        <stop offset=".5" stop-color="#5a5450"/>
        <stop offset="1" stop-color="#1f2023"/>
      </linearGradient>
    </defs>
    <polygon points="730,0 1200,0 1200,533 488,533" fill="#3a3a3a"/>
    <polygon points="760,0 1200,0 1200,533 548,533" fill="url(#heroPhoto)"/>
  </svg>
  <div class="abs hero-title-light">Transform Your Strength</div>
  <div class="abs hero-title-bold">Transform Yourself</div>
  <p class="abs hero-text">Elite coaching, world-class facilities, and a community that pushes you to win — every day. More than a gym — a movement built on grit, performance, and results.</p>
  <div class="abs btn" style="left:112px;top:381px;width:172px;height:46px">Join the Gym</div>
</section>

<!-- locations -->
<h2 class="abs heading" style="top:740px">FIND A CORVANE GYM NEAR YOU</h2>
<div class="abs rule" style="top:789px"></div>
<div class="abs arrow" style="left:58px;top:905px"><svg width="14" height="14" viewBox="0 0 14 14"><path d="M9 2 L4 7 L9 12" stroke="#fff" stroke-width="2.4" fill="none"/></svg></div>
<div class="abs arrow" style="left:1108px;top:905px"><svg width="14" height="14" viewBox="0 0 14 14"><path d="M5 2 L10 7 L5 12" stroke="#fff" stroke-width="2.4" fill="none"/></svg></div>
<div class="abs location" style="left:97px;top:834px">
  <div class="loc-photo" role="img" aria-label="San Diego skyline photo" style="background:linear-gradient(180deg,#7fb6e6 0%,#c9a36a 50%,#2a6fb5 100%)"></div>
  <div class="loc-name">San Diego (HQ)</div>
  <p class="loc-text">Lorem Ipsum is simply dummy text of the printing and type-setting industry.</p>
</div>
<div class="abs location" style="left:352px;top:834px">
  <div class="loc-photo" role="img" aria-label="Boston bridge at night photo" style="background:linear-gradient(180deg,#2f6fd0 0%,#1a3f8c 55%,#3a8be0 100%)"></div>
  <div class="loc-name">Boston</div>
  <p class="loc-text">Lorem Ipsum is simply dummy text of the printing and type-setting industry.</p>
</div>
<div class="abs location" style="left:609px;top:834px">
  <div class="loc-photo" role="img" aria-label="Miami aerial view photo" style="background:linear-gradient(180deg,#b9c9d6 0%,#5c8a5e 55%,#2f6f8a 100%)"></div>
  <div class="loc-name">Miami</div>
  <p class="loc-text">Lorem Ipsum is simply dummy text of the printing and type-setting industry.</p>
</div>
<div class="abs location" style="left:864px;top:834px">
  <div class="loc-photo" role="img" aria-label="Seattle skyline at sunset photo" style="background:linear-gradient(180deg,#e3b58a 0%,#c77a3e 55%,#2e4a2a 100%)"></div>
  <div class="loc-name">Seattle</div>
  <p class="loc-text">Lorem Ipsum is simply dummy text of the printing and type-setting industry.</p>
</div>

<!-- about -->
<div class="abs" role="img" aria-label="Photo of an athlete on an air bike during a competition" style="left:0;top:1235px;width:606px;height:466px;background:linear-gradient(135deg,#3a3b3f 0%,#6b5d52 50%,#2b2c30 100%)"></div>
<div class="abs" style="left:606px;top:1235px;width:594px;height:466px;background:var(--green)"></div>
<h2 class="abs about-title">About Us</h2>
<div class="abs" style="left:669px;top:1372px;width:61px;height:3px;background:var(--white)"></div>
<p class="abs about-text">Lorem ipsum dolor sit amet, consectetur adipisicing elit, sed do eiusmod tempor iont incididunt ut labore et dolore magna aliqua. Ut enim ad minim veniam, quis nos-trudti exercitation ullamco laboris nisi ut aliquip ex ea commodo consequat.</p>
<div class="abs btn" style="left:669px;top:1568px;width:153px;height:39px;font-size:15px">Read More</div>

<!-- programs -->
<h2 class="abs heading" style="top:1823px">PROGRAMS BUILT FOR EVERY ATHLETE</h2>
<div class="abs rule" style="top:1873px"></div>
<div class="abs arrow" style="left:58px;top:2102px"><svg width="14" height="14" viewBox="0 0 14 14"><path d="M9 2 L4 7 L9 12" stroke="#fff" stroke-width="2.4" fill="none"/></svg></div>
<div class="abs arrow" style="left:1108px;top:2102px"><svg width="14" height="14" viewBox="0 0 14 14"><path d="M5 2 L10 7 L5 12" stroke="#fff" stroke-width="2.4" fill="none"/></svg></div>
<div class="abs program" style="left:111px">
  <div class="program-photo" role="img" aria-label="Athlete performing on a competition floor" style="background:linear-gradient(180deg,#2a2a2e,#55504e)"></div>
  <h3>Functional Fitness</h3>
  <p>Risus commodo viverra maecenas accumsan lacus vel facilisis.</p>
  <div class="btn">Read More</div>
</div>
<div class="abs program" style="left:449px">
  <div class="program-photo" role="img" aria-label="Two competitors training side by side" style="background:linear-gradient(180deg,#4a4642,#7a6a5c)"></div>
  <h3>Competitive</h3>
  <p>Risus commodo viverra maecenas accumsan lacus vel facilisis.</p>
  <div class="btn">Read More</div>
</div>
<div class="abs program" style="left:786px">
  <div class="program-photo" role="img" aria-label="Athlete in a bright gym hall" style="background:linear-gradient(180deg,#8a8a8c,#c9c4c0)"></div>
  <h3>Nutrition</h3>
  <p>Risus commodo viverra maecenas accumsan lacus vel facilisis.</p>
  <div class="btn">Read More</div>
</div>

<!-- testimonials -->
<div class="abs" style="left:0;top:2442px;width:1200px;height:545px;background:var(--mint)"></div>
<h2 class="abs heading" style="top:2525px">WHAT PEOPLE SAY</h2>
<div class="abs rule" style="top:2575px"></div>
<div class="abs quote-card">
  <p>Lorem ipsum dolor sit amet, consectetur adipisicing elit, sed do eiusmod tempor incididunt ut labore et dolore magna aliqua. Ut enim ad minim veniam. Quis nostrud exercitation ullamco laboris nisi ut aliquip ex ea commodo consequat. Duis aute irure dolor.Lorem ipsum dolor sit amet, consectetur adipisicing elit, sed do eiusmod tempor incididunt ut labore et dolore magna aliqua.</p>
  <div class="quote-name">John Doe</div>
</div>
<svg class="abs" style="left:440px;top:2800px" width="26" height="14"><polygon points="0,0 26,0 13,13" fill="#fff"/></svg>
<div class="abs avatar" role="img" aria-label="Reviewer portrait" style="left:442px;background:#6d6560"></div>
<div class="abs avatar" role="img" aria-label="Reviewer portrait" style="left:512px;background:#c98a3e"></div>
<div class="abs avatar" role="img" aria-label="Reviewer portrait" style="left:581px;background:#8a5a46"></div>
<div class="abs avatar" role="img" aria-label="Reviewer portrait" style="left:649px;background:#b7aba3"></div>
<div class="abs avatar" role="img" aria-label="Reviewer portrait" style="left:718px;background:#6e7f78"></div>

<!-- newsletter -->
<section class="abs newsletter"></section>
<h2 class="abs heading" style="top:3080px;color:var(--white);font-size:34px">STAY STRONG. STAY CONNECTED.</h2>
<div class="abs" style="left:570px;top:3132px;width:61px;height:3px;background:var(--white)"></div>
<p class="abs news-text">Join the Corvane community and get exclusive training tips, athlete insights, event<br>updates, and special offers — straight to your inbox.</p>
<div class="abs email-input">Your Email Address</div>
<div class="abs btn" style="left:745px;top:3254px;width:173px;height:46px;font-size:17px">Subscribe</div>

<!-- contact -->
<svg class="abs" style="left:112px;top:3510px" width="44" height="34" viewBox="0 0 44 34"><rect x="1.5" y="1.5" width="41" height="31" rx="2" fill="none" stroke="#1f6cb5" stroke-width="2"/><path d="M2 3 L22 19 L42 3" fill="none" stroke="#1f6cb5" stroke-width="2"/></svg>
<div class="abs contact-head" style="left:180px;top:3495px">Email</div>
<div class="abs contact-text" style="left:177px;top:3522px">info@corvaneathletics.com</div>

<svg class="abs" style="left:521px;top:3503px" width="32" height="44" viewBox="0 0 32 44"><rect x="2" y="1.5" width="28" height="41" rx="4" fill="none" stroke="#1f6cb5" stroke-width="2"/><line x1="2" y1="8" x2="30" y2="8" stroke="#1f6cb5" stroke-width="2"/><line x1="2" y1="35" x2="30" y2="35" stroke="#1f6cb5" stroke-width="2"/><line x1="13" y1="39" x2="19" y2="39" stroke="#1f6cb5" stroke-width="2"/></svg>
<div class="abs contact-head" style="left:588px;top:3495px">Phone</div>
<div class="abs contact-text" style="left:580px;top:3522px">+1 555 014 2290</div>

<svg class="abs" style="left:866px;top:3501px" width="42" height="46" viewBox="0 0 42 46"><path d="M21 40 C21 40 8 26 8 17 A13 13 0 0 1 34 17 C34 26 21 40 21 40 Z" fill="none" stroke="#1f6cb5" stroke-width="2"/><circle cx="21" cy="17" r="5" fill="none" stroke="#1f6cb5" stroke-width="2"/><path d="M10 32 L2 44 L40 44 L32 32" fill="none" stroke="#1f6cb5" stroke-width="2"/></svg>
<div class="abs contact-head" style="left:943px;top:3495px">Address</div>
<div class="abs contact-text" style="left:933px;top:3524px">123,  Corvane Athletics<br>fitness Na 12356.</div>

<div class="abs" style="left:512px;top:3600px;width:40px;height:40px;border-radius:6px;background:var(--link)"></div>
<div class="abs" style="left:520px;top:3608px;width:24px;height:24px;border-radius:50%;background:var(--white)"></div>
<div class="abs footer-social" style="left:563px;top:3608px;width:24px;height:24px;border-radius:6px"></div>
<div class="abs footer-social" style="left:615px;top:3608px;width:24px;height:24px;border-radius:4px"></div>
<div class="abs footer-social" style="left:661px;top:3610px;width:26px;height:20px;border-radius:6px"></div>

<!-- footer -->
<footer class="abs footer">Copyright © 2025  Corvane Athletics. All rights reserved.</footer>

</body>
</html>
```